Web Design Project

Psychotherapy and Counselling Practice needs a landing page web design.

My business "Larkfield Advisory" specialises in the treatment of Anxiety and Depression with a holistic approach, endeavouring to unlock the key that holds us to ransom in a life that is imbalanced, frustrating, and ultimately of our own making due to our own perceptions and behaviours.

There is much that impacts us which we cannot change, but we are always in control of how we think, and how we frame our experiences.....learning to challenge those thoughts and behaviours that are destructive and disempowering opens up a world of joyful possibility. Life is about making choices, learn to make wiser and healthier choices.......

Larkfield Advisory has a client base of individual clients but will seek to expand to offer services to the Corporate world by offering an adjunct to employers for established "Wellness Programs".

Larkfield Advisory is a highly professional, ethically bound business, with the needs of the client at the forefront of all we do.

Larkfield Advisory wishes to avoid the usual "jargon driven" psychobabble offered on many counselling web pages. It aims to be stylishly presented, clean in look and with as few "words" as possible and a largely white background (faster loading and more powerful impact of what is stated), those words contained in the webpage should be meaningful, persuasive and have an impact simply at glance. Larkfield does not want , or expect, those prospective clients in need of support , to be reading through volumes of industry driven cliches.

At this point Larkfield is just looking for a high quality landing page. However in time this will likely expand to include other sections such as case studies, video content etc.

Target Market(s)

Those in need of emotional support, suffering mental health issues, and those simply wanting to become self aware supported by a mindful therapist.

Industry/Entity Type

Industry

Requirements
Must have
• The design must incorporate the Larkfield logo and colour schemes found on the attached files.

```html
<!DOCTYPE html>
<html lang="en">
<head>
<meta charset="utf-8">
<title>Larkfield Advisory</title>
<link href="https://fonts.googleapis.com/css2?family=Ubuntu:wght@400;500;700&display=swap" rel="stylesheet">
<style>
  :root {
    --green: #8aac12;
    --green-deep: #7da100;
    --grey: #6c6c6c;
    --grey-text: #8a8a8a;
    --ink: #333;
    --panel: #fbfbfb;
    --white: #fff;
  }
  * { box-sizing: border-box; margin: 0; padding: 0; }
  html, body { width: 1200px; height: 1000px; overflow: hidden; background: var(--white); }
  body { position: relative; font-family: "Ubuntu", sans-serif; color: var(--ink); }

  .nav { position: absolute; left: 119px; top: 122px; width: 485px; height: 48px; background: var(--green); display: flex; align-items: center; }
  .nav a { color: var(--white); text-decoration: none; font-size: 14px; letter-spacing: 2px; font-weight: 500; position: absolute; top: 16px; }

  .brand-tile { position: absolute; left: 665px; top: 43px; width: 108px; height: 107px; background: var(--grey); border-radius: 3px; display: flex; align-items: center; justify-content: center; color: var(--green); font-size: 16px; letter-spacing: 0.5px; }
  .practitioner { position: absolute; left: 782px; top: 40px; color: var(--grey-text); letter-spacing: 2.5px; }
  .practitioner .name { font-size: 19px; font-weight: 500; letter-spacing: 4px; }
  .practitioner .creds { font-size: 13px; margin-top: 6px; }
  .practitioner .contact { font-size: 13.5px; margin-top: 26px; line-height: 22px; }

  .hero { position: absolute; left: 119px; top: 170px; width: 961px; height: 580px; background: var(--panel); overflow: hidden; }
  .hero-mark { position: absolute; left: 64px; top: 262px; font-size: 66px; color: var(--green); letter-spacing: 1px; font-weight: 400; }
  .hero-wave { position: absolute; left: 0; bottom: 0; }

  .welcome-title { position: absolute; left: 624px; top: 187px; width: 447px; text-align: center; color: var(--green-deep); font-size: 14px; font-weight: 500; letter-spacing: 2px; }
  .welcome-copy { position: absolute; left: 624px; top: 221px; width: 440px; font-size: 10.5px; line-height: 13px; letter-spacing: 1.6px; color: var(--ink); }

  .session-photo { position: absolute; left: 624px; top: 336px; width: 447px; height: 297px; background: linear-gradient(135deg, #d9c9a8 0%, #b98f5e 45%, #7b8ea8 100%); }
  .session-photo .label { position: absolute; left: 18px; top: 10px; font-size: 10px; color: var(--green); letter-spacing: 1.5px; font-weight: 700; }

  .tagline-band { position: absolute; left: 119px; top: 750px; width: 485px; height: 125px; background: var(--panel); }
  .tagline { position: absolute; left: 138px; top: 793px; display: flex; align-items: center; gap: 6px; }
  .tagline .chip { background: var(--grey); color: var(--green); font-size: 22px; padding: 0 12px; height: 40px; line-height: 40px; border-radius: 2px; }
  .tagline .firm { color: var(--green); font-size: 14px; letter-spacing: 1.5px; }
  .tagline .claim { color: #555; font-size: 14px; letter-spacing: 2.5px; margin-left: 4px; }

  .social { position: absolute; left: 145px; top: 889px; display: flex; gap: 16px; }
  .social span { width: 20px; height: 20px; border-radius: 50%; background: #111; display: block; }
  .web-address { position: absolute; left: 237px; top: 890px; font-size: 14px; letter-spacing: 2.5px; color: #555; }
  .web-address b { color: var(--green); font-weight: 400; }

  .news-title { position: absolute; left: 665px; top: 763px; width: 360px; text-align: center; color: var(--green); font-size: 14px; letter-spacing: 2.5px; }
  .news-copy { position: absolute; left: 665px; top: 790px; width: 360px; height: 120px; background: var(--panel); padding: 18px 10px 0; text-align: center; font-size: 8.5px; line-height: 12.8px; letter-spacing: 1px; color: var(--ink); }

  .footer { position: absolute; left: 119px; top: 923px; width: 961px; height: 55px; background: var(--green-deep); color: var(--white); font-size: 8px; font-weight: 700; letter-spacing: 1.5px; padding: 21px 0 0 29px; }
</style>
</head>
<body>
  <nav class="nav">
    <a href="#" style="left:30px">Home</a>
    <a href="#" style="left:118px">About Us</a>
    <a href="#" style="left:233px">Contact</a>
    <a href="#" style="left:342px">Our services</a>
  </nav>

  <div class="brand-tile">Larkfield</div>
  <div class="practitioner">
    <div class="name">MARA ELLISON</div>
    <div class="creds">BA (Psych) BSc (Hons) Psych MBPS</div>
    <div class="contact">Mobile: 0400 218 637<br>E-mail: mara.ellison@larkmail.net</div>
  </div>

  <section class="hero">
    <div class="hero-mark">LARKFIELD</div>
    <svg class="hero-wave" width="961" height="110" viewBox="0 0 961 110">
      <path d="M0 110 L0 42 C200 40 520 24 961 14 L961 110 Z" fill="var(--grey)"/>
      <path d="M0 36 C250 34 560 20 961 8 L961 14 C560 26 250 40 0 44 Z" fill="#fff"/>
      <path d="M0 28 C260 24 600 10 870 6 C600 16 260 30 0 34 Z" fill="var(--green)"/>
    </svg>
  </section>

  <h2 class="welcome-title">Welcome to Larkfield</h2>
  <p class="welcome-copy">“Lorem ipsum dolor sit amet, consectetur adipisicing elit,sed do eiusmod tempor incididunt ut labore et dolore magna aliqua. Ut enim ad minim veniam,quis nostrud exercitation ullamco laboris nisi ut aliquip ex ea commodo consequat.Duis aute irure dolor in reprehenderit in voluptate velit esse cillum dolore eu fugiat nulia pariatur. Excepteur sint occaecat cupidatat non proident,sunt in culpa qui officia deserunt mollit anim id est laborum.”</p>

  <div class="session-photo" role="img" aria-label="Photo of a counselling session in a bright living room">
    <span class="label">Slide Video or image</span>
  </div>

  <div class="tagline-band"></div>
  <div class="tagline">
    <span class="chip">Larkfield</span>
    <span class="firm">Advisory</span>
    <span class="claim">is highly Professional</span>
  </div>

  <div class="social"><span></span><span></span></div>
  <div class="web-address">www.<b>larkfieldadvisory</b>.com.au</div>

  <h2 class="news-title">What’s News</h2>
  <p class="news-copy">“Lorem ipsum dolor sit amet, consectetur adipisicing elit,sed do eiusmod tempor incididunt ut labore et dolore magna aliqua. Ut enim ad minim veniam,quis nostrud exercitation ullamco laboris nisi ut aliquip ex ea commodo consequat. Duis aute irure dolor in reprehenderit in voluptate velit esse cillum dolore eu fugiat nulla pariatur. Excepteur sint occaecat cupidatat non proident, sunt in culpa qui officia deserunt mollit anim id est laborum.”</p>

  <footer class="footer">Copyright Larkfield 2013</footer>
</body>
</html>
```